Etiketten für Bio Seifen
Zielgruppe
Wir stellen hochwertig 'handgemachte' Bio-Seifen her. Die Zielgruppe ist von 3-99 Jahren und zusätzlich haben wir auch noch Seife für Hunde.
Der Firmenname ist 'Verdolina'
Aufgabenstellung
Das Etikett soll Bezug auf Natur, Bio, Nachhaltigkeit nehmen. Wir stellen uns 'weiche' Aquarellfarben vor...Seife: Lavendel, Calendular, 7 Kräuter etc.
Das Etikett soll auf eine Beutelschachtel. Die Schachtel hat eine Anmaße: Breite 55mm; Höhe 120mm; Tiefe 30mm
Das Etikett soll im vorderen- und hinteren Bereich zusammenhängend geklebt werden.
Das Etikett soll eine Abmaße von: Breite 51mm; Höhe 114mm haben (Vorderseite) Rückseite gleich.
Wir möchten die Produkte auch gerne nummerieren, d.h. jede Seife hat eine Nummer die nicht zu groß dargestellt werden soll aber trotzdem gut leserlich.
Wir haben noch ein paar Bilder hochgeladen wie wir uns das ungefähr vorstellen.

```html
<!DOCTYPE html>
<html lang="de">
<head>
<meta charset="utf-8">
<title>Verdolina – Seifenetiketten Lavendel</title>
<link rel="stylesheet" href="https://fonts.googleapis.com/css2?family=Montserrat:wght@500;700&family=Dancing+Script:wght@600&display=swap">
<style>
  :root {
    --stage: #000000;
    --note: #ffffff;
    --paper: #f7f6f2;
    --teal: #2f9585;
    --green: #4c9a5e;
    --rose: #f2a9a6;
    --blush: #f8d6cf;
    --lilac: #b9a3d6;
    --leaf: #8ccfb0;
    --butter: #f3e7a4;
  }
  * { box-sizing: border-box; margin: 0; padding: 0; }
  html, body { width: 1200px; height: 1007px; overflow: hidden; background: var(--stage); }
  .canvas { position: relative; width: 1200px; height: 1007px; }

  .note {
    position: absolute; left: 640px; top: 38px; width: 385px;
    text-align: center; color: var(--note);
    font: 500 26px "Montserrat", sans-serif;
  }
  .note svg { display: block; margin: 8px auto 0; }

  .label {
    position: absolute; top: 110px; width: 385px; height: 860px;
    overflow: hidden;
  }
  .label--front { left: 175px; }
  .label--back  { left: 640px; }

  .label__floral {
    position: absolute; inset: 0;
    background:
      radial-gradient(circle at 22% 38%, var(--rose) 0 14%, transparent 30%),
      radial-gradient(circle at 78% 48%, #e8595b 0 5%, transparent 14%),
      radial-gradient(circle at 30% 10%, var(--leaf) 0 10%, transparent 26%),
      radial-gradient(circle at 70% 20%, var(--lilac) 0 8%, transparent 22%),
      radial-gradient(circle at 15% 90%, var(--rose) 0 10%, transparent 24%),
      radial-gradient(circle at 85% 88%, var(--leaf) 0 10%, transparent 26%),
      radial-gradient(circle at 60% 60%, var(--butter) 0 8%, transparent 24%),
      linear-gradient(180deg, var(--blush), #eef3e3 50%, var(--blush));
  }

  .badge {
    position: absolute; top: 64px; left: 50%; transform: translateX(-50%);
    width: 78px; height: 78px; background: var(--paper);
    display: flex; align-items: center; justify-content: center;
  }
  .badge__disc {
    width: 54px; height: 54px; border-radius: 50%; background: var(--teal);
    display: flex; align-items: center; justify-content: center;
    color: var(--paper); font: 700 15px "Montserrat", sans-serif;
  }

  .panel {
    position: absolute; left: 50px; right: 50px; top: 470px; height: 270px;
    background: var(--paper);
    display: flex; flex-direction: column; align-items: center; justify-content: center;
    text-align: center;
  }
  .panel__claim {
    color: var(--teal); font: 500 13px/1.5 "Montserrat", sans-serif;
    letter-spacing: 0.28em; text-transform: uppercase;
  }
  .panel__variety {
    color: var(--green); font: 600 52px/1.1 "Dancing Script", cursive;
    margin: 10px 0 4px;
  }
  .panel__rule { width: 44px; height: 2px; background: var(--green); margin: 8px 0 16px; }
  .panel__brand {
    color: var(--teal); font: 700 17px "Montserrat", sans-serif;
    letter-spacing: 0.22em; text-transform: uppercase;
  }
  .panel__year {
    color: var(--teal); font: 500 12px "Montserrat", sans-serif;
    letter-spacing: 0.2em; margin-top: 8px;
  }
</style>
</head>
<body>
<main class="canvas">
  <p class="note">Rückseite mit Hundepfote...?
    <svg width="14" height="16" viewBox="0 0 14 16" aria-hidden="true">
      <path d="M7 1v13M2 9l5 5 5-5" fill="none" stroke="var(--note)" stroke-width="1.6"/>
    </svg>
  </p>

  <article class="label label--front">
    <div class="label__floral" role="img" aria-label="Aquarell-Blumenmuster in Rosa, Grün und Lavendel"></div>
    <div class="badge"><span class="badge__disc">No 1</span></div>
    <section class="panel">
      <p class="panel__claim">Handgemachte<br>Seife</p>
      <h2 class="panel__variety">Lavendel</h2>
      <span class="panel__rule"></span>
      <p class="panel__brand">Verdolina</p>
      <p class="panel__year">2022</p>
    </section>
  </article>

  <article class="label label--back">
    <div class="label__floral" role="img" aria-label="Aquarell-Blumenmuster in Rosa, Grün und Lavendel"></div>
    <div class="badge">
      <span class="badge__disc">
        <svg width="28" height="28" viewBox="0 0 28 28" aria-label="Pfotensymbol" role="img">
          <g fill="var(--paper)">
            <ellipse cx="14" cy="19" rx="6.5" ry="5.5"/>
            <ellipse cx="6" cy="12" rx="2.6" ry="3.3"/>
            <ellipse cx="11" cy="7" rx="2.6" ry="3.3"/>
            <ellipse cx="17" cy="7" rx="2.6" ry="3.3"/>
            <ellipse cx="22" cy="12" rx="2.6" ry="3.3"/>
          </g>
        </svg>
      </span>
    </div>
    <section class="panel">
      <p class="panel__claim">Handgemachte<br>Seife</p>
      <h2 class="panel__variety">Lavendel</h2>
      <span class="panel__rule"></span>
      <p class="panel__brand">Verdolina</p>
      <p class="panel__year">2022</p>
    </section>
  </article>
</main>
</body>
</html>
```